Local fast-growing company in the service sector

We are looking for a modern business card design, which should also appear on our letterheads

Target Market(s)

Private and industrial sectors

Contact Information for Business Card

Vorname Name
Kellberger Str. 18
74521 Lindhofen
Tel.: 07146-839214-0
Name@agentur-kvtl.de

Colors
9d9d9d
919191
aaaaaa

Requirements
Must have
• The logo (file) in silver

```html
<!DOCTYPE html>
<html lang="de">
<head>
<meta charset="utf-8">
<title>KVTL Visitenkarte</title>
<link rel="stylesheet" href="https://fonts.googleapis.com/css2?family=Roboto:wght@400;500;700;900&family=Roboto+Condensed:wght@500&display=swap">
<style>
  :root {
    --page-bg: #e9e7e4;
    --card-dark: #1b1c1e;
    --card-light: #f4f4f4;
    --silver: #9d9d9d;
    --silver-mid: #919191;
    --silver-light: #aaaaaa;
    --text-dark: #4a4a4a;
    --white: #ffffff;
  }
  * { margin: 0; padding: 0; box-sizing: border-box; }
  html, body {
    width: 1200px; height: 960px; overflow: hidden;
    background: var(--page-bg);
    font-family: "Roboto", Arial, sans-serif;
  }
  .canvas { position: relative; width: 1200px; height: 960px; }

  .card {
    position: absolute;
    border-radius: 22px;
    box-shadow: 0 3px 8px rgba(0,0,0,0.25);
    overflow: hidden;
  }

  /* back side */
  .card-back {
    left: 320px; top: 98px; width: 610px; height: 355px;
    background: var(--card-dark);
  }
  .card-back .brand {
    position: absolute; left: 0; right: 0; top: 124px;
    display: flex; align-items: center; justify-content: center; gap: 18px;
  }
  .brand-square {
    width: 46px; height: 46px; background: var(--silver-light); border-radius: 6px;
  }
  .card-back .brand-name {
    font-weight: 900; font-size: 74px; color: var(--silver-light); letter-spacing: 2px;
    line-height: 1;
  }
  .card-back .web {
    position: absolute; left: 0; right: 0; top: 294px;
    text-align: center; color: var(--white);
    font-size: 15px; letter-spacing: 7px;
  }

  /* front side */
  .card-front {
    left: 320px; top: 492px; width: 600px; height: 343px;
    background: var(--card-light);
  }
  .name-band {
    position: absolute; left: 0; top: 53px; width: 225px; height: 95px;
    background: linear-gradient(90deg, #8a8a8a 0%, var(--silver-light) 55%, #d9d9d9 100%);
  }
  .person-name {
    position: absolute; left: 37px; top: 88px;
    font-family: "Roboto Condensed", "Roboto", sans-serif;
    font-weight: 500; font-size: 21px; color: var(--white);
  }
  .front-brand {
    position: absolute; left: 190px; top: 58px;
    display: flex; align-items: center; gap: 22px;
  }
  .front-brand .brand-square { width: 90px; height: 90px; background: var(--silver); border-radius: 8px; }
  .front-brand .brand-name {
    font-weight: 900; font-size: 64px; color: var(--silver); letter-spacing: 1px; line-height: 1;
  }
  .contact {
    position: absolute; left: 305px; top: 183px;
    color: var(--text-dark); font-size: 15px; line-height: 19px;
  }
  .address { margin-bottom: 10px; }
  .contact-list { list-style: none; }
  .contact-list li { display: flex; align-items: center; gap: 8px; }
  .contact-list svg { width: 13px; height: 13px; fill: #6a6a6a; flex: none; }
</style>
</head>
<body>
<div class="canvas">

  <section class="card card-back" aria-label="Kartenrückseite">
    <div class="brand">
      <span class="brand-square"></span>
      <span class="brand-name">KVTL</span>
    </div>
    <p class="web">www.agentur-kvtl.de</p>
  </section>

  <section class="card card-front" aria-label="Kartenvorderseite">
    <div class="name-band"></div>
    <p class="person-name">LUKAS BERNER</p>
    <div class="front-brand">
      <span class="brand-square"></span>
      <span class="brand-name">KVTL</span>
    </div>
    <div class="contact">
      <p class="address">Kellberger Str. 18<br>74521 Lindhofen</p>
      <ul class="contact-list">
        <li>
          <svg viewBox="0 0 16 16" aria-hidden="true"><path d="M3.5 1 6 3.8 4.6 5.6c.9 2 2.6 3.8 4.8 4.8l1.8-1.4L15 11.5 13.3 14.6C7 14.4 1.6 9 1.4 2.7z"/></svg>
          <span>07146-839214-0</span>
        </li>
        <li>
          <svg viewBox="0 0 16 16" aria-hidden="true"><path d="M1 3h14v2L8 9 1 5z M1 6.5 8 10.5l7-4V13H1z"/></svg>
          <span>Name@agentur-kvtl.de</span>
        </li>
        <li>
          <svg viewBox="0 0 16 16" aria-hidden="true"><circle cx="8" cy="8" r="7"/><path d="M5 4c1.5 1 1 2.5 2.5 3S8 9.5 7 11M10 3c0 2 2.5 2 3.5 4" stroke="#f4f4f4" stroke-width="1.3" fill="none"/></svg>
          <span>www.agentur-kvtl.de</span>
        </li>
      </ul>
    </div>
  </section>

</div>
</body>
</html>
```